Business Card Design for Marketing Firm

Looking for business card design for higher end marketing firm. Clean but impressionable/trendy. We are a marketing firm that represents manufacturers in the foodservice equipment and supply industry. Our customers are end users such has hotels, restaurants, country clubs, convention centers and casinos as well as distributors of restaurants supplies and equipment, and manufacturers of foodservice equipment and supplies.
Target Market(s)
Hotels, Restaurants, Supply & Equipment Distributors, Foodservice Manufacturers
Industry/Entity Type
Foodservice/Hospitality
Contact Information for Business Card
Name, Title, Contact Number, Email, Website, Social Media, Address
Requirements
Must have
- Clean & Simple but Serious and Impressionable

```html
<!DOCTYPE html>
<html lang="en">
<head>
<meta charset="utf-8">
<title>Harbor Service Reps – Business Card</title>
<link rel="stylesheet" href="https://fonts.googleapis.com/css2?family=Open+Sans:wght@300;400;600;700&family=Cormorant+Garamond:wght@500&display=swap">
<style>
  :root {
    --navy: #27286f;
    --paper: #ffffff;
    --canvas: #eeeeee;
    --tab-shadow: #c9c9cf;
  }
  * { box-sizing: border-box; margin: 0; padding: 0; }
  html, body { width: 864px; height: 1200px; overflow: hidden; background: var(--canvas); }
  .sheet { position: relative; width: 864px; height: 1200px; }

  .card {
    position: absolute; left: 72px; width: 720px; height: 412px;
    background: var(--paper);
    box-shadow: 0 10px 22px rgba(0,0,0,0.18);
    overflow: hidden;
  }
  .card--front { top: 150px; }
  .card--back { top: 638px; }
  .card-shapes { position: absolute; inset: 0; width: 100%; height: 100%; }

  .name-tab {
    position: absolute; left: 0; top: 44px; width: 377px; height: 67px;
    background: var(--paper);
    box-shadow: 3px 4px 6px rgba(0,0,0,0.25);
    display: flex; align-items: center; padding-left: 82px;
  }
  .name-tab__text {
    font-family: "Open Sans", sans-serif; font-weight: 600; font-size: 31px;
    color: var(--navy); letter-spacing: -0.5px;
  }

  .contact-list { position: absolute; left: 44px; top: 172px; list-style: none; }
  .contact-list li {
    display: flex; align-items: center; height: 42px;
    font-family: "Open Sans", sans-serif; font-weight: 300; font-size: 22px; color: var(--paper);
  }
  .contact-list svg { width: 18px; height: 18px; margin-right: 18px; fill: var(--paper); flex: none; }
  .contact-list strong { font-weight: 400; }

  .brand-name {
    position: absolute;
    font-family: "Cormorant Garamond", serif; font-weight: 500;
    color: var(--navy); letter-spacing: 1.5px; text-transform: uppercase; white-space: nowrap;
    text-align: center;
  }
  .brand-name--front { left: 460px; width: 260px; top: 182px; font-size: 21px; }
  .brand-name--back { left: 0; width: 720px; top: 196px; font-size: 38px; }

  .web-tab-text {
    position: absolute; left: 190px; width: 344px; top: 336px;
    font-family: "Open Sans", sans-serif; font-weight: 400; font-size: 18px;
    color: var(--navy); text-align: center;
  }
</style>
</head>
<body>
<main class="sheet">

  <section class="card card--front" aria-label="Business card front">
    <svg class="card-shapes" viewBox="0 0 720 412" aria-hidden="true">
      <polygon points="0,0 324,0 448,412 0,412" fill="var(--navy)"/>
      <rect x="444" y="0" width="276" height="21" fill="var(--navy)"/>
      <rect x="571" y="391" width="149" height="21" fill="var(--navy)"/>
    </svg>

    <div class="name-tab"><span class="name-tab__text">YOUR NAME</span></div>

    <ul class="contact-list">
      <li>
        <svg viewBox="0 0 20 20"><circle cx="10" cy="10" r="9" /><path d="M1 10h18M10 1v18" stroke="var(--navy)" stroke-width="1.6" fill="none"/><ellipse cx="10" cy="10" rx="4" ry="9" stroke="var(--navy)" stroke-width="1.6" fill="none"/></svg>
        www.sitename.com
      </li>
      <li>
        <svg viewBox="0 0 20 20"><rect x="1" y="4" width="18" height="13"/><path d="M2 5l8 7 8-7" stroke="var(--navy)" stroke-width="1.8" fill="none"/></svg>
        hello@sitename.com
      </li>
      <li>
        <svg viewBox="0 0 20 20"><path d="M10 1a6.5 6.5 0 0 0-6.5 6.5C3.5 12.5 10 19 10 19s6.5-6.5 6.5-11.5A6.5 6.5 0 0 0 10 1z"/><circle cx="10" cy="7.5" r="2.4" fill="var(--navy)"/></svg>
        Address_<strong>dummytext</strong>
      </li>
      <li>
        <svg viewBox="0 0 20 20"><path d="M4 2l3.5 0 1.5 4-2 1.6c1 2.4 2.8 4.2 5.2 5.2L13.8 11l4 1.5V16c0 1-1 2-2 2C8.5 18 2 11.5 2 4c0-1 1-2 2-2z"/></svg>
        000-000-000
      </li>
    </ul>

    <p class="brand-name brand-name--front">Harbor Service Reps</p>
  </section>

  <section class="card card--back" aria-label="Business card back">
    <svg class="card-shapes" viewBox="0 0 720 412" aria-hidden="true">
      <rect x="0" y="347" width="720" height="65" fill="var(--navy)"/>
      <polygon points="178,347 190,321 204,347" fill="var(--tab-shadow)"/>
      <polygon points="542,347 530,321 516,347" fill="var(--tab-shadow)"/>
      <polygon points="190,321 530,321 516,379 204,379" fill="var(--paper)"/>
    </svg>

    <p class="brand-name brand-name--back">Harbor Service Reps</p>
    <p class="web-tab-text">www.sitename.com</p>
  </section>

</main>
</body>
</html>
```